"Every Small Hand Finds Purpose" Teaching Series

16:9 design
Size: 64"x36" @ 300 dpi
Should include the title: Every Small Hand Finds Purpose
and text subtly "Summer 2017"
Should include the church logo in a subtle way.
This artwork will be printed as a large banner but we will also adapt the artwork to be used in other formats like social media, a weekly bulletin, digital signage etc.
We are looking for a graphic that captures the message of the series: God has gifted people with a variety of gifts, abilities and resources to be used in service to Him.
We would like to see designs with bright jewel tones with a modern feel. Attached are examples of designs we like.
Overview of the series: God’s people are diverse: personalities, generations, gifts, abilities, career, resources, skills etc. Many people who are only briefly mentioned in the New Testament had a lasting impact because they used their God given gifts to serve. They opened their home, mentored others, prayed, gave generously, or served in practical ways. God uses all types of people and service for His glory. Some people think that their gifts are small, ordinary or that their work doesn’t matter. This is not the case in God’s eyes. Every person is empowered by God to use his/her gifts to service and that matters for impacting eternity. God has given us all we need to join him in His mission.
Church

```html
<!DOCTYPE html>
<html lang="en">
<head>
<meta charset="utf-8">
<title>Every Small Hand Finds Purpose — Summer 2017</title>
<link rel="stylesheet" href="https://fonts.googleapis.com/css2?family=Ultra&family=Alfa+Slab+One&family=Roboto+Condensed:wght@300;400&display=swap">
<style>
  :root {
    --paper: #f3f1ef;
    --tile-a: #ebe7e3;
    --tile-b: #f2efec;
    --tile-line: rgba(255, 255, 255, 0.75);
    --fill-a: #7b6a5e;
    --fill-b: #4f423a;
    --fill-c: #9a8a7e;
    --fill-d: #3a302b;
    --text: #2b2b2b;
    --teal: #1a7f78;
    --sky: #6cc3dd;
    --amber: #f4a21c;
    --red: #e0262c;
    --plum: #3e2448;
    --blue: #2d58a8;
  }
  html, body {
    margin: 0;
    padding: 0;
    width: 1200px;
    height: 677px;
    overflow: hidden;
    background: var(--paper);
  }
  .series-banner {
    position: relative;
    width: 1200px;
    height: 677px;
    overflow: hidden;
  }
  .portrait-wall {
    position: absolute;
    inset: 0;
    background:
      repeating-linear-gradient(90deg, transparent 0 112px, var(--tile-line) 112px 114px),
      repeating-linear-gradient(0deg, transparent 0 112px, var(--tile-line) 112px 114px),
      radial-gradient(ellipse at 50% 45%, rgba(214, 200, 188, 0.35) 0%, transparent 70%),
      repeating-conic-gradient(var(--tile-a) 0 25%, var(--tile-b) 0 50%) 0 0 / 228px 228px;
  }
  .series-title {
    position: absolute;
    left: 44px;
    top: -6px;
    margin: 0;
    font-family: "Ultra", "Alfa Slab One", "Rockwell Extra Bold", "Rockwell", serif;
    font-weight: 400;
    font-size: 112px;
    line-height: 137px;
    letter-spacing: 0;
    text-transform: uppercase;
    background:
      linear-gradient(160deg, rgba(255, 255, 255, 0.12) 0%, rgba(0, 0, 0, 0.15) 100%),
      repeating-linear-gradient(90deg, transparent 0 112px, rgba(255, 255, 255, 0.35) 112px 114px),
      repeating-linear-gradient(0deg, transparent 0 112px, rgba(255, 255, 255, 0.35) 112px 114px),
      repeating-conic-gradient(var(--fill-a) 0 25%, var(--fill-b) 0 50%) 0 0 / 228px 228px,
      var(--fill-c);
    -webkit-background-clip: text;
    background-clip: text;
    color: transparent;
  }
  .series-title span { display: block; }
  .church-mark {
    position: absolute;
    right: 42px;
    top: 56px;
    display: flex;
    align-items: center;
    gap: 12px;
    font-family: "Roboto Condensed", sans-serif;
    font-weight: 400;
    font-size: 24px;
    color: var(--plum);
    letter-spacing: 1px;
    text-transform: uppercase;
  }
  .church-mark .mark-square {
    width: 34px;
    height: 34px;
    background: var(--teal);
  }
  .season {
    position: absolute;
    right: 42px;
    top: 556px;
    text-align right;
  }
  .season-label {
    margin: 0;
    font-family: "Roboto Condensed", sans-serif;
    font-weight: 300;
    font-size: 46px;
    line-height: 48px;
    color: var(--text);
    letter-spacing: 0.5px;
    text-align: right;
  }
  .jewel-bars { display: block; margin-top: 6px; }
</style>
</head>
<body>
  <main class="series-banner">
    <div class="portrait-wall" role="img" aria-label="Faded grid of smiling portraits of diverse people of many ages and backgrounds"></div>

    <h1 class="series-title" role="img" aria-label="Every Small Hand Finds Purpose — title letters filled with a mosaic of portrait photos">
      <span>Every</span>
      <span>Small</span>
      <span>Hand</span>
      <span>Finds</span>
      <span>Purpose</span>
    </h1>

    <div class="church-mark">
      <span class="mark-square"></span>
      <span class="mark-name">Harbor Light Church</span>
    </div>

    <div class="season">
      <p class="season-label">SUMMER 2017</p>
      <svg class="jewel-bars" width="315" height="13" viewBox="0 0 315 13" aria-hidden="true">
        <rect x="0" y="0" width="47" height="13" fill="var(--teal)"/>
        <rect x="53.6" y="0" width="47" height="13" fill="var(--sky)"/>
        <rect x="107.2" y="0" width="47" height="13" fill="var(--amber)"/>
        <rect x="160.8" y="0" width="47" height="13" fill="var(--red)"/>
        <rect x="214.4" y="0" width="47" height="13" fill="var(--plum)"/>
        <rect x="268" y="0" width="47" height="13" fill="var(--blue)"/>
      </svg>
    </div>
  </main>
</body>
</html>
```